Envelope Design - Winner can do follow-up business

- Varnoko.com is a Swiss-based online store selling business shirts and accessories for business men
- Please visit the webpage to make yourself familiar with the company. Although the text is in German, with Plimbo translator you should be able to understand the main content.
- Our clients are mainly business men between 30 and 60 years old. Mostly with a high income working in the service industry (banking, insurance, lawyers, etc.). Sometimes there wives purchase the shirts for them ;-)
- The colors and the logo are given, as they are also used for the print materials (please see files in attachment)
- I am running several businesses and often need a talented web designer --> the winner gets substantial follow-up business
your task:
-for our company we need a new envelope design
-It should be simple and modern
-please use one of the logos in the followings.
-suprise me :)

```html
<!DOCTYPE html>
<html lang="en">
<head>
<meta charset="utf-8">
<title>Varnoko Envelope Set</title>
<link rel="stylesheet" href="https://fonts.googleapis.com/css2?family=Lexend+Exa:wght@400&family=Roboto+Slab:wght@400&display=swap">
<style>
  :root {
    --backdrop: #dcd7cf;
    --paper: #ffffff;
    --paper-shade: #eef0f3;
    --edge: #b9b9b9;
    --brand-red: #ee2e24;
    --brand-red-soft: #f47f62;
    --brand-yellow: #e6d66b;
    --brand-yellow-soft: #f2eab2;
    --ink: #1d1d1d;
  }
  * { margin: 0; padding: 0; box-sizing: border-box; }
  html, body { width: 1200px; height: 942px; overflow: hidden; }
  body { position: relative; background: var(--backdrop); font-family: "Roboto Slab", Georgia, serif; }

  .envelope {
    position: absolute;
    width: 963px;
    height: 455px;
    background: var(--paper);
    border: 1px solid var(--edge);
    overflow: hidden;
  }
  .envelope--back-red { left: 190px; top: 47px; height: 453px; border: none; }
  .envelope--back-yellow { left: 100px; top: 234px; background: linear-gradient(110deg, var(--paper-shade), var(--paper)); }
  .envelope--front { left: 47px; top: 438px; }

  .flap { position: absolute; left: 0; top: 0; width: 963px; height: 160px; }
  .flap-name {
    position: absolute; left: 0; width: 100%; text-align: center;
    font-family: "Lexend Exa", Arial, sans-serif; font-size: 26px; letter-spacing: 2px;
  }
  .envelope--back-red .flap-name { top: 62px; color: var(--brand-red-soft); }
  .envelope--back-yellow .flap-name { top: 50px; color: var(--brand-yellow-soft); }

  .sender { position: absolute; left: 18px; top: 70px; }
  .sender-name {
    font-family: "Lexend Exa", Arial, sans-serif; font-size: 34px; letter-spacing: 1px;
    color: var(--brand-yellow); line-height: 1;
  }
  .sender-address {
    display: flex; gap: 10px; margin-top: 20px; margin-left: 8px;
    font-size: 19px; line-height: 25px; color: var(--ink);
  }
  .sender-address svg { flex: none; margin-top: 2px; }

  .footer-band { position: absolute; left: 0; bottom: 0; width: 963px; height: 62px; }
  .website {
    position: absolute; left: 26px; bottom: 12px; display: flex; align-items: center; gap: 10px;
    font-size: 19px; color: var(--ink);
  }
</style>
</head>
<body>

<section class="envelope envelope--back-red" aria-label="Envelope back with red flap">
  <svg class="flap" viewBox="0 0 963 160" aria-hidden="true">
    <path fill="var(--brand-red)" d="M2,0 H963 C955,35 945,68 905,80 L510,148 Q481,153 452,148 L60,80 C20,68 10,35 2,0Z"/>
  </svg>
  <div class="flap-name">VARNOKO</div>
</section>

<section class="envelope envelope--back-yellow" aria-label="Envelope back with yellow flap">
  <svg class="flap" viewBox="0 0 963 160" aria-hidden="true">
    <path fill="var(--brand-yellow)" d="M0,0 H963 C955,35 945,68 905,80 L510,148 Q481,153 452,148 L58,80 C18,68 8,35 0,0Z"/>
  </svg>
  <div class="flap-name">VARNOKO</div>
</section>

<section class="envelope envelope--front" aria-label="Envelope front">
  <div class="sender">
    <div class="sender-name">VARNOKO</div>
    <div class="sender-address">
      <svg width="16" height="22" viewBox="0 0 16 22" aria-hidden="true">
        <path fill="var(--brand-red)" d="M8,0 C3.6,0 0,3.5 0,7.9 C0,13.5 8,22 8,22 C8,22 16,13.5 16,7.9 C16,3.5 12.4,0 8,0Z"/>
        <circle cx="8" cy="8" r="3.2" fill="var(--paper)"/>
      </svg>
      <p>Street Name, City Name<br>State Zipcode</p>
    </div>
  </div>

  <svg class="footer-band" viewBox="0 0 963 62" aria-hidden="true">
    <rect x="0" y="6" width="963" height="56" fill="var(--brand-yellow)"/>
    <rect x="0" y="2" width="963" height="3" fill="var(--brand-red)"/>
    <path fill="var(--paper)" d="M826,0 H933 L879,42Z"/>
  </svg>
  <div class="website">
    <svg width="22" height="22" viewBox="0 0 22 22" aria-hidden="true" fill="none" stroke="var(--brand-red)" stroke-width="1.6">
      <circle cx="11" cy="11" r="9.5"/>
      <ellipse cx="11" cy="11" rx="4.2" ry="9.5"/>
      <path d="M1.5,11 H20.5 M3,6 H19 M3,16 H19"/>
    </svg>
    <span>www.varnoko.com</span>
  </div>
</section>

</body>
</html>
```